Accountant website

Please design a accountant website for www.fenwaybridgeadvisory.com.au. This site is majorly out of date, and is not supported by modern browsers.

The style should use the reds from the design at dev.fenwaybridgeadvisory.com.au, and should be modern and make use of Slides (large content slides that the user scrolls through on the front page).

The content is largely already on the site, however happy to move some around to suit the modern design as required.

The dev.fenwaybridgeadvisory.com.au was a rough mock up that I have completed that the client is "happy" with the direction, however this needs a lot of polish and finishing touches, and I will accept designs that differ from this, but highly recommend that this is used as a guide.

Ready to be sliced PSD Only - HTML no required.

In all honesty, although I can technically do a lot of this, the polished finished I want for this site has eluded me in a few attempts, and therefore I am looking out there at you much more artistic people to finish (or redesign if required) this site.

Target Market(s)

Higher end Small - Medium Business

Industry/Entity Type

Accountant

Requirements
Must have
• Must use the logo from dev.fenwaybridgeadvisory.com.au use exactly the red colours as defined in this layout. A basic layout PSD (to get the colour etc) and the logo in ai format is attached to this project. Please ignore the SSL warning on the development site.

The final product does NOT have to be the same as shown on dev.fenwaybridgeadvisory.com.au however the red colour scheme must be used. The client DOES want the logo on the RIGHT.

Must have a front landing page design, and a page layout that considers the other page content (at least one separate PSD)
Nice to have
• I really am looking at a slide format for the front page simular to:

http://www.quillo.com/au/
http://www.vaultmoor.com/

The attached photos should be used on the site. Was considering a rotating banner with these images are a watermark background on a solid Red header bar, but happy to be shown other options.
Should not have
• Please no "Layout Goblin" submissions.

```html
<!DOCTYPE html>
<html lang="en">
<head>
<meta charset="utf-8">
<title>Fenway Bridge Advisory</title>
<link href="https://fonts.googleapis.com/css2?family=PT+Sans:wght@400;700&family=PT+Sans+Narrow:wght@400;700&family=Source+Sans+3:wght@300;400;600&display=swap" rel="stylesheet">
<style>
:root{
  --red:#b5262b;
  --red-dark:#8c1519;
  --red-deep:#6e0f12;
  --ink:#2b2b2b;
  --text:#555;
  --muted:#888;
  --line:#dcdcdc;
  --panel:#f2f2f2;
  --footer:#2e2e2e;
  --footer-dark:#1f1f1f;
  --white:#fff;
}
*{box-sizing:border-box;margin:0;padding:0}
html,body{width:698px;height:1200px;overflow:hidden}
body{position:relative;background:var(--white);font-family:"PT Sans",sans-serif;color:var(--text)}
.abs{position:absolute}
.topline{left:0;top:0;width:698px;height:3px;background:#9a9a9a}
.header{left:0;top:3px;width:698px;height:73px;background:linear-gradient(#fff,#f3f3f3)}
.brand{left:60px;top:26px;display:flex;align-items:center;gap:8px}
.brand-mark{width:12px;height:12px;background:var(--red)}
.brand-name{font-family:"PT Sans Narrow",sans-serif;font-weight:700;font-size:19px;color:var(--ink);letter-spacing:.3px}
.account{right:58px;top:17px;font-family:"PT Sans Narrow",sans-serif;font-size:8.5px;color:#555;letter-spacing:.2px}
.account span{margin:0 5px;color:#aaa}
.search{left:518px;top:51px;width:122px;height:16px;border:1px solid #ccc;background:#fff;font-size:7.5px;color:#999;padding:3px 11px}
.search svg{position:absolute;right:6px;top:3px}
.nav{left:0;top:76px;width:698px;height:28px;background:linear-gradient(#c3343a,var(--red) 50%,#9b1d22);border-bottom:1px solid var(--red-deep)}
.nav ul{list-style:none;display:flex;position:absolute;left:70px;top:5px}
.nav li{font-family:"PT Sans Narrow",sans-serif;font-size:10px;color:#fff;padding:4px 5px;margin-right:12.5px;line-height:10px}
.nav li.current{background:var(--red-deep);border-radius:2px}
.hero{left:0;top:104px;width:698px;height:242px;background:linear-gradient(135deg,#ece7df 0%,#d8d4cc 35%,#e9d5c2 60%,#dcd9d2 100%)}
.hero-arrow{top:210px;width:26px;height:26px;border-radius:50%;background:rgba(255,255,255,.85);border:1px solid #ccc}
.hero-arrow svg{position:absolute;left:8px;top:7px}
.hero-caption{left:58px;top:310px;width:582px;height:36px;background:rgba(245,245,245,.88)}
.hero-caption p{position:absolute;left:91px;top:9px;font-family:"PT Sans Narrow",sans-serif;font-weight:700;font-size:15.5px;color:#333}
.hero-btn{left:394px;top:6px;width:83px;height:23px;background:linear-gradient(#555,#2f2f2f);border-radius:3px;color:#fff;font-family:"PT Sans Narrow",sans-serif;font-size:11px;padding:4px 8px}
.hero-btn b{color:#999;margin-left:4px;font-weight:400}
.services{left:0;top:346px;width:698px;height:95px;background:linear-gradient(#f7f7f7,#fff)}
.service{top:12px;width:180px;text-align:center}
.service svg{display:block;margin:0 auto 10px}
.service h3{font-family:"PT Sans Narrow",sans-serif;font-weight:700;font-size:11px;color:var(--red);line-height:16px}
.rule{left:58px;width:582px;height:1px;background:var(--line)}
.intro{left:80px;top:458px;width:538px;text-align:center}
.intro h2{font-family:"Source Sans 3",sans-serif;font-weight:300;font-size:18px;color:#333;margin-bottom:8px}
.intro p{font-size:8.3px;line-height:14.5px;color:#666}
.photo{background:linear-gradient(#c9d6e0,#b7bec3 55%,#9fa6a8);border:2px solid #c8c8c8}
.principal-photo{left:64px;top:561px;width:181px;height:104px}
.principal{left:259px;top:557px;width:376px}
h2.section{font-family:"Source Sans 3",sans-serif;font-weight:300;font-size:17.5px;color:var(--red);margin-bottom:9px}
.principal p,.team p{font-size:7.2px;line-height:12px;color:#666;text-align:justify;margin-bottom:5px}
.more{color:var(--red);font-family:"PT Sans Narrow",sans-serif;font-size:8px}
.team{left:62px;top:714px;width:380px}
.team .more{display:block;margin-top:-5px}
.avatar{top:719px;width:58px;height:58px;border-radius:50%;border:2px solid #fff;box-shadow:0 0 0 1px #ddd;background:linear-gradient(#8fb0d0,#5f7fa0)}
.steps{left:65px;top:843px;list-style:none}
.steps li{font-family:"Source Sans 3",sans-serif;font-size:10.2px;color:#444;height:30.5px}
.steps li b{font-weight:400;color:#888;margin-right:6px}
.steps li.active{color:var(--red)}
.steps li.active b{color:var(--red)}
.step-panel{left:245px;top:839px;width:396px;height:114px;background:var(--panel);border-left:1px solid var(--line);padding:14px 14px}
.step-panel h4{font-family:"Source Sans 3",sans-serif;font-weight:400;font-size:10.5px;color:#222;margin-bottom:8px}
.step-panel p{font-size:7.5px;line-height:16px;color:#666}
.news{left:0;top:980px;width:698px;height:70px;background:#f4f4f4;border-top:1px solid var(--line);border-bottom:1px solid var(--line)}
.news-label{left:60px;top:16px;width:82px;text-align:center}
.news-label span{display:block;font-family:"Source Sans 3",sans-serif;font-size:11.5px;color:var(--red);margin-top:5px}
.news-divider{left:146px;top:6px;width:1px;height:58px;background:#d0d0d0}
.news-text{left:159px;top:16px;width:480px;font-size:7.6px;line-height:12.5px;color:#555}
.news-text time{display:block;color:#222;margin-top:3px}
.partners{left:58px;top:1066px;width:582px;display:flex;justify-content:space-between;align-items:center}
.partners span{font-family:"Source Sans 3",sans-serif;font-weight:600;font-size:13px;color:#7d7d7d}
.footer{left:0;top:1106px;width:698px;height:94px;background:linear-gradient(var(--footer),var(--footer-dark))}
.footer ul{list-style:none;display:flex;position:absolute;left:70px;top:14px}
.footer li{font-family:"PT Sans Narrow",sans-serif;font-size:10px;color:#cfcfcf;padding:0 5px;margin-right:12.5px}
.footer-rule{left:58px;top:38px;width:582px;height:1px;background:#474747}
.copy{left:58px;top:52px;font-size:8px;line-height:19px;color:#aaa}
.badge{left:489px;top:54px;display:flex;align-items:center;gap:7px}
.badge i{width:24px;height:24px;border-radius:50%;background:#fff;border:3px solid var(--red)}
.badge span{font-family:"PT Sans Narrow",sans-serif;font-weight:700;font-size:8px;color:#ccc;line-height:9px}
.foot-brand{left:580px;top:58px;font-family:"PT Sans Narrow",sans-serif;font-weight:700;font-size:11px;color:#8a8a8a;line-height:11px}
</style>
</head>
<body>
<div class="abs topline"></div>
<header class="abs header">
  <div class="abs brand"><i class="brand-mark"></i><span class="brand-name">FENWAY BRIDGE ADVISORY</span></div>
  <div class="abs account">CLIENT LOGIN<span>::</span>REGISTER</div>
  <div class="abs search">Search
    <svg width="10" height="10" viewBox="0 0 10 10"><circle cx="4" cy="4" r="3" fill="none" stroke="#222" stroke-width="1.6"/><line x1="6" y1="6" x2="9.5" y2="9.5" stroke="#222" stroke-width="2"/></svg>
  </div>
</header>
<nav class="abs nav">
  <ul><li class="current">HOME</li><li>ABOUT US</li><li>SERVICES</li><li>WORKING WITH US</li><li>CONTACT US</li><li>LINKS</li><li>TESTIMONIALS</li><li>NEWS</li><li>ARTICLES</li></ul>
</nav>
<section class="abs hero" role="img" aria-label="Stressed office worker buried under scattered paperwork"></section>
<div class="abs hero-arrow" style="left:56px"><svg width="8" height="10" viewBox="0 0 8 10"><path d="M6 1 2 5l4 4" fill="none" stroke="#999" stroke-width="1.4"/></svg></div>
<div class="abs hero-arrow" style="left:615px"><svg width="8" height="10" viewBox="0 0 8 10"><path d="M2 1l4 4-4 4" fill="none" stroke="#999" stroke-width="1.4"/></svg></div>
<div class="abs hero-caption">
  <p>Too musch bookkeeping let us take the load off</p>
  <div class="abs hero-btn">CONTACT US<b>›</b></div>
</div>
<section class="abs services">
  <div class="abs service" style="left:65px">
    <svg width="22" height="26" viewBox="0 0 22 26"><path d="M6 2h3v10h2V8h3v4h1v-3h3v4h1v-2h2v9l-3 5H8l-5-8 2-1 2 3V2z" fill="var(--red)"/></svg>
    <h3>BUSINESS ESTABLISHMENT</h3>
  </div>
  <div class="abs service" style="left:259px">
    <svg width="30" height="26" viewBox="0 0 30 26"><rect x="2" y="17" width="4" height="7" fill="var(--red)"/><rect x="8" y="14" width="4" height="10" fill="var(--red)"/><rect x="14" y="11" width="4" height="13" fill="var(--red)"/><rect x="20" y="8" width="4" height="16" fill="var(--red)"/><path d="M2 14 10 8l5 3 10-8" fill="none" stroke="var(--red)" stroke-width="1.6"/><path d="M22 2h5v5z" fill="var(--red)"/></svg>
    <h3>MANAGEMENT DURING BUSINESS<br>GROWTH &amp; MATURITY</h3>
  </div>
  <div class="abs service" style="left:453px">
    <svg width="28" height="26" viewBox="0 0 28 26"><circle cx="14" cy="12" r="5.5" fill="none" stroke="var(--red)" stroke-width="1.6"/><rect x="11.5" y="18" width="5" height="4" fill="var(--red)"/><g stroke="var(--red)" stroke-width="1.4"><line x1="14" y1="1" x2="14" y2="4"/><line x1="4" y1="12" x2="7" y2="12"/><line x1="21" y1="12" x2="24" y2="12"/><line x1="7" y1="5" x2="9" y2="7"/><line x1="21" y1="5" x2="19" y2="7"/></g></svg>
    <h3>BUSINESS CESSATION</h3>
  </div>
</section>
<div class="abs rule" style="top:441px"></div>
<section class="abs intro">
  <h2>Building a Relationship with Fenway Bridge Advisory</h2>
  <p>Fenway Bridge Advisory believes that people choose to do business with people, not companies. As a result we provided a brief overview of our service process so that you know what to expect when you meet with Fenway Bridge Advisory. We also take this opportunity to introduce you to our team.</p>
</section>
<div class="abs photo principal-photo" role="img" aria-label="Portrait of the principal standing by a marina"></div>
<section class="abs principal">
  <h2 class="section">The Principal – Helena Marsh</h2>
  <p>Helena achieved her Bachelor of Commerce degree from the University of Kestrel Bay in 2001 and went on to complete her Certified Adviser qualifications. She has been a member of the Institute of Certified Advisers since May 2005.</p>
  <p>With over 11 years experience in the accounting profession, working with high profile businesses within the Kestrel Bay area, Helena has developed a great understanding of the varying needs of different businesses within their industries. <span class="more">MORE</span></p>
</section>
<div class="abs rule" style="top:690px"></div>
<section class="abs team">
  <h2 class="section">The Team</h2>
  <p>Helena is supported by a team of 3 staff who understand the importance of developing and maintaining client relationships. The team are dedicated to providing you with the best possible service which exceeds your expectations.</p>
  <span class="more">MEET THE TEAM...</span>
</section>
<div class="abs avatar" style="left:453px" role="img" aria-label="Team member portrait"></div>
<div class="abs avatar" style="left:515px" role="img" aria-label="Team member portrait"></div>
<div class="abs avatar" style="left:576px" role="img" aria-label="Team member portrait"></div>
<div class="abs rule" style="top:816px"></div>
<ul class="abs steps">
  <li class="active"><b>»</b>Complimentary Client Consultation</li>
  <li><b>»</b>Customised Accounting Solution</li>
  <li><b>»</b>Quote Acceptance</li>
  <li><b>»</b>Ongoing Business Advice</li>
</ul>
<section class="abs step-panel">
  <h4>Complimentary Client Consultation</h4>
  <p>MeetingA one-hour meeting is held at a mutually convenient time to enable us to learn about you and your business. Throughout which the focus is on your business. We discuss the challenges you face in your business, and brainstorm how we can assist you with overcoming these challenges. We also discuss your goals and the future direction you want your business to take.</p>
</section>
<section class="abs news">
  <div class="abs news-label">
    <svg width="20" height="16" viewBox="0 0 20 16"><rect x="1" y="1" width="18" height="14" fill="none" stroke="var(--red)" stroke-width="1.6"/><rect x="4" y="4" width="5" height="4" fill="var(--red)"/><g stroke="var(--red)" stroke-width="1.2"><line x1="11" y1="5" x2="16" y2="5"/><line x1="11" y1="8" x2="16" y2="8"/><line x1="4" y1="11" x2="16" y2="11"/></g></svg>
    <span>Latest News</span>
  </div>
  <div class="abs news-divider"></div>
  <div class="abs news-text">Nulla condimentum orci vitae augue rutrum venenatis. Sed erat leo, varius id magna sit amet, pellentesque eleifend ligula. Nulla non massa id neque lobortis vestibulum.<time>October 12 - 2013</time></div>
</section>
<div class="abs partners">
  <span>Larkmead</span><span>Quorvi</span><span>Netterly</span><span>Tallis</span><span>Corvane</span><span>Ostrel</span><span>Brightwell</span><span>Pennick</span><span>Valdra</span>
</div>
<footer class="abs footer">
  <ul><li>HOME</li><li>ABOUT US</li><li>SERVICES</li><li>WORKING WITH US</li><li>CONTACT US</li><li>LINKS</li><li>TESTIMONIALS</li><li>NEWS</li><li>ARTICLES</li></ul>
  <div class="abs footer-rule"></div>
  <div class="abs copy">Copyright © 2013 fenwaybridgeadvisory.com.au<br>All rights reserved</div>
  <div class="abs badge"><i></i><span>Certified<br>Advisers</span></div>
  <div class="abs foot-brand">FENWAY<br>BRIDGE</div>
</footer>
</body>
</html>
```